Business Card Design Project

I need a business card designed from scratch. I have an existing logo that I can upload in Illustrator for modification or redesign.

The Company is called Query Lanterns http://querylanterns.com.au and we provide Search Engine Optimization services to Australian businesses. The current logo signifies an increase in visitors, profits etc...

There are no restrictions as to the redesign - colours, style etc are all open to change.

Cards will be full colour and one sided printed at http://www.cardmoxel.com.au so check their requirements for file format and sizes etc.

I will expect all original files upon completion of project.

Target Market(s)

Any business with a web site looking to improve their search engine rankings

Industry/Entity Type

Business

Requirements
Must have
• I like modern, sleek designs. Clean, not fussy, uncluttered.

```html
<!DOCTYPE html>
<html lang="en">
<head>
<meta charset="utf-8">
<title>Query Lanterns – Business Card</title>
<link href="https://fonts.googleapis.com/css2?family=Open+Sans:wght@400;600;700&display=swap" rel="stylesheet">
<style>
  :root {
    --stage: #d9d9d9;
    --card: #000000;
    --brand-blue: #1f78bd;
    --ink-light: #ffffff;
    --icon-glyph: #ffffff;
  }
  * { margin: 0; padding: 0; box-sizing: border-box; }
  html, body {
    width: 1200px; height: 393px; overflow: hidden;
    background: var(--stage);
    font-family: "Open Sans", Arial, sans-serif;
  }
  .canvas { position: relative; width: 1200px; height: 393px; }
  .card {
    position: absolute; top: 35px; width: 565px; height: 323px;
    background: var(--card); border-radius: 22px; overflow: hidden;
  }
  .card--front { left: 18px; }
  .card--back { left: 617px; }

  .brand-name {
    position: absolute; left: 0; right: 0; top: 128px;
    text-align: center; color: var(--brand-blue);
    font-size: 52px; font-weight: 700; letter-spacing: -0.5px;
    line-height: 1;
  }

  .holder {
    position: absolute; right: 32px; top: 62px;
    color: var(--brand-blue); font-size: 17px; white-space: nowrap;
  }
  .holder__name { font-weight: 700; font-size: 20px; }

  .contact-list {
    position: absolute; right: 24px; top: 148px; list-style: none;
  }
  .contact-list li {
    display: flex; justify-content: flex-end; align-items: center;
    height: 20px; margin-bottom: 4px;
    color: var(--ink-light); font-size: 13px; white-space: nowrap;
  }
  .contact-list li.contact--address { margin-top: 10px; }
  .contact-list b { font-weight: 700; margin-right: 4px; }
  .contact-icon { width: 14px; height: 14px; margin-left: 12px; flex: none; }
</style>
</head>
<body>
<main class="canvas">
  <section class="card card--front" aria-label="Card front">
    <h1 class="brand-name">Query Lanterns</h1>
  </section>

  <section class="card card--back" aria-label="Card back">
    <p class="holder"><span class="holder__name">Name</span> | Administrator</p>
    <ul class="contact-list">
      <li><b>Phone.</b> 001-123-123456
        <svg class="contact-icon" viewBox="0 0 14 14"><circle cx="7" cy="7" r="7" fill="var(--brand-blue)"/><path d="M4.6 3.8 L6 3.6 6.4 5.4 5.6 6 Q6.3 7.7 8 8.4 L8.6 7.6 10.4 8 10.2 9.4 Q6.5 9.8 4.6 3.8Z" fill="var(--icon-glyph)"/></svg></li>
      <li><b>Fax.</b> 001-123-123456
        <svg class="contact-icon" viewBox="0 0 14 14"><circle cx="7" cy="7" r="7" fill="var(--brand-blue)"/><rect x="5" y="3.5" width="4" height="2.5" fill="var(--icon-glyph)"/><rect x="3.5" y="6" width="7" height="3.5" fill="var(--icon-glyph)"/><rect x="5" y="9" width="4" height="1.8" fill="var(--icon-glyph)"/></svg></li>
      <li><b>Cell.</b> 001-123-123456
        <svg class="contact-icon" viewBox="0 0 14 14"><circle cx="7" cy="7" r="7" fill="var(--brand-blue)"/><rect x="5" y="3" width="4" height="8" rx="0.8" fill="var(--icon-glyph)"/><rect x="5.7" y="4" width="2.6" height="4.5" fill="var(--brand-blue)"/></svg></li>
      <li><b>Email.</b> hello@querylanterns.com.au
        <svg class="contact-icon" viewBox="0 0 14 14"><circle cx="7" cy="7" r="7" fill="var(--brand-blue)"/><text x="7" y="10" text-anchor="middle" font-size="9" font-weight="700" fill="var(--icon-glyph)" font-family="Open Sans, sans-serif">@</text></svg></li>
      <li><b>Web.</b> www.Website.com
        <svg class="contact-icon" viewBox="0 0 14 14"><circle cx="7" cy="7" r="7" fill="var(--brand-blue)"/><circle cx="7" cy="7" r="3.5" fill="none" stroke="var(--icon-glyph)" stroke-width="1"/><path d="M3.5 7 H10.5 M7 3.5 V10.5" stroke="var(--icon-glyph)" stroke-width="0.8"/></svg></li>
      <li class="contact--address">25 Street Name, Road Name, State, Country Code
        <svg class="contact-icon" viewBox="0 0 14 14"><circle cx="7" cy="7" r="7" fill="var(--brand-blue)"/><path d="M7 3.3 L10.6 6.6 H9.5 V10.3 H4.5 V6.6 H3.4Z" fill="var(--icon-glyph)"/></svg></li>
    </ul>
  </section>
</main>
</body>
</html>
```